Road Construction Company needs business cards

We would like a new business card designed for our business.

We're a road construction company based in Qld, Australia.

Can the business card please have the following information on it.

Name: Warren Halbeck
Position: General Manager
Phone: 0472 915 348
Email: Warren.halbeck@tovrin.com.au
Address: 87 Marrow Ave, Pendlebay, QLD, 4023
Website: www.tovrin.com.au

Visually we'd like the card to be professional and simple.

Attached is our logo.

Our website is www.tovrin.com.au

Target Market(s)

Men aged 25-60

Contact Information for Business Card

As listed in project description

Font styles to use
Serif

Requirements
Must have
• Large logo on back of card

```html
<!DOCTYPE html>
<html lang="en">
<head>
<meta charset="utf-8">
<title>Tovrin Business Card</title>
<link href="https://fonts.googleapis.com/css2?family=Montserrat:wght@400;500;600;800&display=swap" rel="stylesheet">
<style>
  :root {
    --backdrop: #e4e4e4;
    --brand-blue: #0d4a9c;
    --brand-blue-dark: #0a4393;
    --brand-blue-light: #1668ae;
    --card-white: #f1f1f1;
    --text-grey: #6a6a6a;
    --logo-white: #f2efec;
  }
  * { margin: 0; padding: 0; box-sizing: border-box; }
  html, body {
    width: 1200px;
    height: 1200px;
    overflow: hidden;
    background: var(--backdrop);
    font-family: "Montserrat", sans-serif;
  }
  .card {
    position: absolute;
    left: 227px;
    width: 705px;
    height: 403px;
  }
  .card-front {
    top: 155px;
    background: linear-gradient(200deg, var(--brand-blue-light) 0%, var(--brand-blue) 55%, var(--brand-blue-dark) 100%);
    display: flex;
    align-items: center;
    justify-content: center;
  }
  .card-back {
    top: 610px;
    background: linear-gradient(120deg, #e6e6e6 0%, var(--card-white) 60%, #f5f5f5 100%);
  }
  .brand-name {
    font-family: "Montserrat", sans-serif;
    font-weight: 800;
    letter-spacing: 4px;
    line-height: 1;
  }
  .card-front .brand-name {
    color: var(--logo-white);
    font-size: 92px;
  }
  .card-back .brand-name {
    position: absolute;
    left: 52px;
    top: 170px;
    color: var(--brand-blue);
    font-size: 52px;
    letter-spacing: 2px;
  }
  .contact-block {
    position: absolute;
    left: 356px;
    top: 92px;
    color: var(--text-grey);
  }
  .person-name {
    color: var(--brand-blue);
    font-weight: 600;
    font-size: 30px;
    line-height: 1.2;
  }
  .person-role {
    font-size: 18px;
    margin-top: 6px;
  }
  .address {
    font-size: 19px;
    line-height: 25px;
    margin-top: 17px;
  }
  .contact-list {
    list-style: none;
    margin-top: 14px;
    font-size: 19px;
  }
  .contact-list li {
    display: flex;
    align-items: center;
    height: 27px;
  }
  .contact-list svg {
    width: 16px;
    height: 16px;
    margin-right: 9px;
    fill: var(--brand-blue);
    flex: none;
  }
</style>
</head>
<body>
  <section class="card card-front">
    <div class="brand-name">TOVRIN</div>
  </section>

  <section class="card card-back">
    <div class="brand-name">TOVRIN</div>

    <div class="contact-block">
      <h1 class="person-name">Warren Halbeck</h1>
      <p class="person-role">General Manager</p>
      <p class="address">87 Marrow Ave, Pendlebay,<br>QLD, 4023</p>
      <ul class="contact-list">
        <li>
          <svg viewBox="0 0 24 24" aria-hidden="true"><path d="M6.6 10.8a15.1 15.1 0 0 0 6.6 6.6l2.2-2.2a1 1 0 0 1 1-.25 11.4 11.4 0 0 0 3.6.57 1 1 0 0 1 1 1V20a1 1 0 0 1-1 1A17 17 0 0 1 3 4a1 1 0 0 1 1-1h3.5a1 1 0 0 1 1 1c0 1.25.2 2.45.57 3.57a1 1 0 0 1-.25 1z"/></svg>
          0472 915 348
        </li>
        <li>
          <svg viewBox="0 0 24 24" aria-hidden="true"><path d="M2 5h20v14H2z M2 5l10 8 10-8" fill="none" stroke="#0d4a9c" stroke-width="0"/><path d="M2 5h20v2l-10 7L2 7z"/><path d="M2 9l10 7 10-7v10H2z"/></svg>
          Warren.halbeck@tovrin.com.au
        </li>
        <li>
          <svg viewBox="0 0 24 24" aria-hidden="true"><path d="M12 2a10 10 0 1 0 0 20 10 10 0 0 0 0-20zm7.9 9h-3.4a15 15 0 0 0-1.3-6.1A8 8 0 0 1 19.9 11zM12 4c.9 1.2 2.3 3.7 2.5 7h-5C9.7 7.7 11.1 5.2 12 4zM4.1 13h3.4a15 15 0 0 0 1.3 6.1A8 8 0 0 1 4.1 13zm3.4-2H4.1a8 8 0 0 1 4.7-6.1A15 15 0 0 0 7.5 11zM12 20c-.9-1.2-2.3-3.7-2.5-7h5c-.2 3.3-1.6 5.8-2.5 7zm3.2-.9a15 15 0 0 0 1.3-6.1h3.4a8 8 0 0 1-4.7 6.1z"/></svg>
          www.tovrin.com.au
        </li>
      </ul>
    </div>
  </section>
</body>
</html>
```